Modern Business Card

Modern professional business card with more than just logo and demographic info. Something memorable.

We are a trendy/modern chiropractic group with an emphasis on neurology, hence the minimalist-type brain logo. We want to convey that modern and technical aspect with professionalism and the elite nature of our practice environment.

```html
<!DOCTYPE html>
<html lang="en">
<head>
<meta charset="utf-8">
<title>Meridell Chiropractic – Business Card</title>
<link rel="stylesheet" href="https://fonts.googleapis.com/css2?family=Quattrocento:wght@400;700&family=Khand:wght@600&family=Roboto:wght@400&display=swap">
<style>
  :root {
    --backdrop: #b9b9b9;
    --card: #f1f1f1;
    --brand-blue: #3a5f9e;
    --ink-dark: #2a2426;
    --ink-brown: #3f3336;
    --ink-body: #4a4a4a;
  }
  * { margin: 0; padding: 0; box-sizing: border-box; }
  html, body {
    width: 1200px; height: 576px; overflow: hidden;
    background: var(--backdrop);
  }
  .stage { position: relative; width: 1200px; height: 576px; }
  .card {
    position: absolute;
    background: var(--card);
    border-radius: 9px;
    overflow: hidden;
  }

  /* Front */
  .card--front { left: 82px; top: 138px; width: 485px; height: 294px; }
  .front__mark {
    position: absolute; left: 84px; top: 100px;
    width: 62px; height: 62px;
    background: var(--brand-blue);
  }
  .front__wordmark {
    position: absolute; left: 162px; top: 88px;
    font-family: "Quattrocento", serif; font-weight: 400;
    color: var(--ink-dark); line-height: 1;
  }
  .front__wordmark .line-main { display: block; font-size: 44px; letter-spacing: 1px; }
  .front__wordmark .line-sub { display: block; font-size: 25px; letter-spacing: 1px; margin-top: 4px; }
  .front__web {
    position: absolute; left: 0; right: 0; top: 247px;
    text-align: center;
    font-family: "Roboto", sans-serif; font-size: 12px;
    color: var(--ink-dark);
  }
  .front__dash { position: absolute; top: 255px; }
  .front__dash--left { left: 112px; }
  .front__dash--right { left: 340px; }
  .front__band {
    position: absolute; left: 0; bottom: 0; width: 100%; height: 13px;
    display: flex;
  }
  .front__band .band-blue { flex: 1; background: var(--brand-blue); }
  .front__band .band-brown { flex: 1; background: var(--ink-brown); }

  /* Back */
  .card--back { left: 602px; top: 138px; width: 480px; height: 290px; }
  .back__mark {
    position: absolute; left: 80px; top: 58px;
    width: 106px; height: 106px;
    background: var(--brand-blue);
  }
  .back__brand {
    position: absolute; left: 40px; width: 186px; top: 180px;
    text-align: center;
    font-family: "Quattrocento", serif; font-weight: 400;
    font-size: 22px; letter-spacing: 1px;
    color: var(--brand-blue);
  }
  .contact {
    position: absolute; left: 262px; top: 66px;
    font-family: "Quattrocento", serif; color: var(--ink-body);
  }
  .contact__name {
    font-family: "Khand", sans-serif; font-weight: 600;
    font-size: 21px; color: var(--brand-blue); line-height: 1.1;
  }
  .contact__title { font-size: 12.5px; margin-top: 2px; }
  .contact__list { list-style: none; margin-top: 24px; }
  .contact__list li {
    display: flex; align-items: center; gap: 9px;
    font-size: 12.5px; height: 18.5px;
  }
  .contact__list svg { width: 11px; height: 11px; fill: var(--brand-blue); flex: none; }
  .contact__address { font-size: 12.5px; line-height: 18px; margin-top: 8px; }
</style>
</head>
<body>
<main class="stage">

  <section class="card card--front" aria-label="Card front">
    <div class="front__mark" aria-hidden="true"></div>
    <h1 class="front__wordmark">
      <span class="line-main">MERIDELL</span>
      <span class="line-sub">CHIROPRACTIC</span>
    </h1>
    <svg class="front__dash front__dash--left" width="32" height="4" viewBox="0 0 32 4" aria-hidden="true">
      <polygon points="0,2 32,0.5 32,3.5" fill="var(--brand-blue)"/>
    </svg>
    <p class="front__web">www.meridellchiro.com</p>
    <svg class="front__dash front__dash--right" width="32" height="4" viewBox="0 0 32 4" aria-hidden="true">
      <polygon points="0,0.5 32,2 0,3.5" fill="var(--brand-blue)"/>
    </svg>
    <div class="front__band" aria-hidden="true">
      <span class="band-blue"></span><span class="band-brown"></span>
    </div>
  </section>

  <section class="card card--back" aria-label="Card back">
    <div class="back__mark" aria-hidden="true"></div>
    <p class="back__brand">MERIDELL</p>
    <div class="contact">
      <h2 class="contact__name">Marcus Reed</h2>
      <p class="contact__title">Managing Director</p>
      <ul class="contact__list">
        <li>
          <svg viewBox="0 0 12 12" aria-hidden="true"><path d="M1 3.5C1 2 2.5 1.5 6 1.5S11 2 11 3.5V5H8.5V3.8H3.5V5H1Z M2.5 6.5L4 5h4l1.5 1.5V10.5h-7Z"/></svg>
          <span>828-555-0142</span>
        </li>
        <li>
          <svg viewBox="0 0 12 12" aria-hidden="true"><path d="M0.5 2.5h11v7h-11Z M1.5 3.3v0.4L6 7l4.5-3.3v-0.4L6 6.2Z" fill-rule="evenodd"/></svg>
          <span>marcus@meridellchiro.com</span>
        </li>
        <li>
          <svg viewBox="0 0 12 12" aria-hidden="true"><path d="M6 0.8a5.2 5.2 0 1 0 0.01 0Z M6 1.8c-0.8 0.8-1.3 2.3-1.4 3.7h2.8C7.3 4.1 6.8 2.6 6 1.8Z M4.6 6.5c0.1 1.4 0.6 2.9 1.4 3.7 0.8-0.8 1.3-2.3 1.4-3.7Z M1.9 5.5h1.7c0.1-1.2 0.4-2.4 0.9-3.2A4.2 4.2 0 0 0 1.9 5.5Z M8.4 5.5h1.7A4.2 4.2 0 0 0 7.5 2.3c0.5 0.8 0.8 2 0.9 3.2Z M1.9 6.5a4.2 4.2 0 0 0 2.6 3.2c-0.5-0.8-0.8-2-0.9-3.2Z M8.4 6.5c-0.1 1.2-0.4 2.4-0.9 3.2a4.2 4.2 0 0 0 2.6-3.2Z" fill-rule="evenodd"/></svg>
          <span>www.meridellchiro.com</span>
        </li>
      </ul>
      <p class="contact__address">418 Maple Row, Fairview,<br>Asheville, NC 28730</p>
    </div>
  </section>

</main>
</body>
</html>
```